Business card design for new eCommerce site focusing on integrity and strong businsess tactics

We need a business card that will stand out and be memorable. Something with color that matches our company logo colors. Think high end version of Pactivo. There are 2 logos provided. The parent company is called Amber Ledge Partners and we are presenting a new and very exciting eCommerce site called BrightHarborTrade.example.

Target Market(s)

Our target markets are in the Activities, Food and Beverage, Health and Beauty

Industry/Entity Type

Marketing

Contact Information for Business Card

We have 4 members that need cards...I will provide all info to the winner of the design contest
Business Address is
4870 West 63rd Avenue, Suite C207
Phoenix AZ 85731

Font styles to use
Serif
Sans Serif

Colors

Designer to choose colors to be used in the design.

Requirements
Must have
• The card must be memorable...should be unique in design but must exude integrity and be playful .
• I have provided several colors or our parent company...please feel free to use which ever
Nice to have
• I will leave this up to you. Feel free to use other images of your choosing that wraps around our client.....Activities, Dining, Health, Beauty
Should not have
• just dont be boring

```html
<!DOCTYPE html>
<html lang="en">
<head>
<meta charset="utf-8">
<title>BrightHarborTrade.example Business Card</title>
<link href="https://fonts.googleapis.com/css2?family=Jost:wght@400;500;600&display=swap" rel="stylesheet">
<style>
  :root {
    --backdrop: #e9e6e1;
    --card-white: #f7f7f7;
    --brand-blue: #2b7bb0;
    --brand-green: #7dc242;
    --brand-grey: #5e5e5e;
    --text-white: #ffffff;
    --tagline-grey: #555555;
  }
  * { margin: 0; padding: 0; box-sizing: border-box; }
  html, body { width: 1200px; height: 960px; overflow: hidden; }
  body {
    background: var(--backdrop);
    font-family: "Jost", "Futura", sans-serif;
    position: relative;
  }
  .card {
    position: absolute;
    width: 600px;
    height: 343px;
    border-radius: 20px;
    overflow: hidden;
    box-shadow: 0 4px 10px rgba(0,0,0,0.25);
  }
  .card-front { left: 302px; top: 130px; background: var(--card-white); }
  .card-back { left: 299px; top: 490px; background: var(--brand-blue); }
  .front-surface { position: absolute; inset: 0; }
  .brand-mark {
    position: absolute;
    left: 70px;
    top: 68px;
    display: flex;
    align-items: center;
    gap: 12px;
  }
  .brand-dot {
    width: 34px; height: 34px; border-radius: 50%;
    background: var(--brand-blue);
  }
  .brand-name {
    font-size: 31px;
    font-weight: 500;
    color: var(--brand-green);
    letter-spacing: -0.3px;
  }
  .brand-tagline {
    position: absolute;
    left: 190px;
    top: 110px;
    font-size: 15px;
    letter-spacing: 1.2px;
    color: var(--tagline-grey);
  }
  .person {
    position: absolute;
    right: 322px;
    top: 226px;
    text-align: right;
    color: var(--text-white);
    font-size: 14.5px;
    line-height: 19px;
  }
  .person-name {
    font-size: 22px;
    line-height: 26px;
    color: var(--brand-green);
    font-weight: 400;
    text-transform: uppercase;
  }
  .divider {
    position: absolute;
    left: 296px;
    top: 228px;
    width: 2px;
    height: 82px;
    background: var(--text-white);
  }
  .contact-list {
    position: absolute;
    left: 316px;
    top: 230px;
    list-style: none;
    color: var(--text-white);
    font-size: 14px;
  }
  .contact-list li {
    display: flex;
    align-items: center;
    gap: 9px;
    height: 19.5px;
  }
  .contact-list svg { width: 13px; height: 13px; flex: none; }
  .parent-mark {
    position: absolute;
    left: 0; right: 0;
    top: 72px;
    display: flex;
    flex-direction: column;
    align-items: center;
    gap: 48px;
  }
  .parent-dot {
    width: 70px; height: 70px; border-radius: 50%;
    border: 4px solid var(--text-white);
  }
  .parent-name {
    font-size: 37px;
    font-weight: 600;
    color: var(--text-white);
  }
</style>
</head>
<body>
  <section class="card card-front">
    <svg class="front-surface" width="600" height="343" viewBox="0 0 600 343">
      <path d="M0,178 C180,200 400,196 600,192 L600,343 L0,343 Z" fill="var(--brand-blue)"/>
      <path d="M0,162 C120,180 230,190 330,191 C230,197 110,191 0,174 Z" fill="var(--brand-green)"/>
      <path d="M300,183 C420,160 520,156 600,164 L600,187 C520,178 420,178 300,185 Z" fill="var(--brand-grey)"/>
      <path d="M0,178 C180,200 400,196 600,192" fill="none" stroke="#ffffff" stroke-width="3"/>
    </svg>

    <div class="brand-mark">
      <span class="brand-dot"></span>
      <span class="brand-name">BrightHarborTrade.example</span>
    </div>
    <p class="brand-tagline">Leisure-Eateries-Fitness-Styling</p>

    <div class="person">
      <p class="person-name">Dana Whitlock</p>
      <p>CEO/FOUNDER</p>
      <p>4870 West 63rd Avenue</p>
      <p>Suite C207, Phoenix AZ 85731</p>
    </div>
    <span class="divider"></span>
    <ul class="contact-list">
      <li>
        <svg viewBox="0 0 16 16"><path d="M3 1h3l1.5 4-2 1.3a9 9 0 0 0 4.2 4.2L11 8.5l4 1.5v3a2 2 0 0 1-2 2A13 13 0 0 1 1 3a2 2 0 0 1 2-2z" fill="var(--brand-green)"/></svg>
        555 210 4836
      </li>
      <li>
        <svg viewBox="0 0 16 16"><rect x="4" y="0.5" width="8" height="15" rx="1.5" fill="var(--brand-green)"/><rect x="5.5" y="2.5" width="5" height="8" fill="var(--brand-blue)"/><circle cx="8" cy="13" r="1" fill="var(--brand-blue)"/></svg>
        555 318 7702
      </li>
      <li>
        <svg viewBox="0 0 16 16"><rect x="1" y="3" width="14" height="10" fill="var(--brand-green)"/><path d="M1 3l7 6 7-6" fill="none" stroke="var(--brand-blue)" stroke-width="1.3"/></svg>
        dana@brightharbortrade.example
      </li>
      <li>
        <svg viewBox="0 0 16 16"><circle cx="8" cy="8" r="7" fill="var(--brand-green)"/><path d="M1 8h14M8 1c-3 4-3 10 0 14M8 1c3 4 3 10 0 14" fill="none" stroke="var(--brand-blue)" stroke-width="1"/></svg>
        www.brightharbortrade.example
      </li>
    </ul>
  </section>

  <section class="card card-back">
    <div class="parent-mark">
      <span class="parent-dot"></span>
      <span class="parent-name">Amber Ledge Partners</span>
    </div>
  </section>
</body>
</html>
```